BUSINESS CARD DESIGN

NAME- DALE VORSKIN
PHONE NUMER - 555- 714-9082
EMAIL- OFFICE@TRV-GROUNDMAKRZ.COM
BACK OF CARD- SPEACIALIZES IN LAND CLEARING, FORESTRY MUCLHING AND EXCAVATION

Contact Information for Business Card

NAME- DALE VORSKIN PHONE NUMER - 555- 714-9082 EMAIL- OFFICE@TRV-GROUNDMAKRZ.COM BACK OF CARD- SPEACIALIZES IN LAND CLEARING , MUCLHING AND EXCAVATION

```html
<!DOCTYPE html>
<html lang="en">
<head>
<meta charset="utf-8">
<title>Traverse Ground Makrz – Business Card</title>
<link href="https://fonts.googleapis.com/css2?family=Rubik:wght@400;500;700;900&display=swap" rel="stylesheet">
<style>
  :root {
    --stage: #2b2b2b;
    --ink: #121212;
    --gold: #f9b418;
    --white: #ffffff;
    --card-w: 760px;
    --card-h: 434px;
  }
  * { box-sizing: border-box; margin: 0; padding: 0; }
  html, body { width: 1200px; height: 960px; overflow: hidden; }
  body {
    background: var(--stage);
    font-family: "Rubik", sans-serif;
    display: flex; flex-direction: column; align-items: center; justify-content: center;
    gap: 40px;
  }
  .card {
    width: var(--card-w); height: var(--card-h);
    position: relative; overflow: hidden;
    box-shadow: 0 14px 30px rgba(0,0,0,.45);
  }

  /* ---------- front ---------- */
  .card--front { background: var(--ink); }
  .front-band { position: absolute; left: 0; right: 0; height: 26px; background: var(--gold); }
  .front-band--top { top: 0; }
  .front-band--bottom { bottom: 0; }
  .brand {
    position: absolute; display: flex; flex-direction: column; align-items: center; gap: 10px;
    color: var(--gold); text-align: center;
  }
  .brand-mark { width: 34px; height: 34px; border-radius: 50%; background: var(--gold); }
  .brand-name { font-weight: 700; font-size: 24px; letter-spacing: 2px; line-height: 1.15; }
  .brand-phone { font-weight: 700; font-size: 14px; letter-spacing: 5px; }
  .card--front .brand { left: 40px; top: 140px; width: 300px; }
  .front-divider {
    position: absolute; left: 370px; top: 110px; width: 3px; height: 214px; background: var(--gold);
  }
  .person { position: absolute; left: 410px; top: 110px; }
  .person-name { color: var(--gold); font-weight: 900; font-size: 40px; letter-spacing: 1px; line-height: 1; }
  .person-role {
    display: flex; align-items: center; gap: 8px; margin-top: 4px;
    color: var(--gold); font-size: 18px; font-weight: 500;
  }
  .role-mark { display: flex; gap: 4px; }
  .role-mark span { display: block; height: 12px; background: var(--gold); transform: skewX(-30deg); }
  .role-mark span:first-child { width: 44px; }
  .role-mark span:last-child { width: 6px; background: var(--white); }
  .contacts { list-style: none; margin-top: 34px; display: flex; flex-direction: column; gap: 12px; }
  .contact { display: flex; align-items: center; gap: 14px; font-size: 15px; letter-spacing: .5px; color: var(--white); }
  .contact--email { color: var(--gold); }
  .contact-icon {
    width: 22px; height: 22px; border-radius: 50%; background: var(--gold);
    display: flex; align-items: center; justify-content: center; flex: none;
  }
  .contact-icon svg { width: 13px; height: 13px; fill: none; stroke: var(--ink); stroke-width: 2.2; stroke-linecap: round; stroke-linejoin: round; }

  /* ---------- back ---------- */
  .card--back { background: var(--gold); }
  .card--back .brand { color: var(--ink); left: 230px; top: 70px; width: 300px; }
  .card--back .brand-mark { background: var(--ink); }
  .tagline-band {
    position: absolute; left: 0; right: 0; bottom: 44px; height: 62px; background: var(--ink);
    display: flex; align-items: center; justify-content: center;
  }
  .tagline { color: var(--gold); font-weight: 900; font-size: 23px; letter-spacing: .3px; }
  .machine-art {
    position: absolute; background: var(--ink); border-radius: 6px; opacity: .9;
  }
  .machine-art--left { left: 40px; bottom: 106px; width: 180px; height: 140px; }
  .machine-art--right { right: 40px; top: 110px; width: 200px; height: 120px; }
</style>
</head>
<body>

  <section class="card card--front" aria-label="Business card front">
    <div class="front-band front-band--top"></div>
    <div class="brand">
      <span class="brand-mark"></span>
      <span class="brand-name">TRAVERSE GROUND<br>MAKRZ LLC</span>
      <span class="brand-phone">555-714-9082</span>
    </div>
    <div class="front-divider"></div>
    <div class="person">
      <h1 class="person-name">DALE VORSKIN</h1>
      <div class="person-role">
        <span class="role-mark"><span></span><span></span></span>
        Owner
      </div>
      <ul class="contacts">
        <li class="contact">
          <span class="contact-icon"><svg viewBox="0 0 24 24"><path d="M5 3h4l2 5-3 2a11 11 0 0 0 6 6l2-3 5 2v4a2 2 0 0 1-2 2A17 17 0 0 1 3 5a2 2 0 0 1 2-2z"/></svg></span>
          555- 714-9082
        </li>
        <li class="contact contact--email">
          <span class="contact-icon"><svg viewBox="0 0 24 24"><rect x="3" y="5" width="18" height="14" rx="2"/><path d="M3 7l9 6 9-6"/></svg></span>
          OFFICE@TRV-GROUNDMAKRZ.COM
        </li>
        <li class="contact">
          <span class="contact-icon"><svg viewBox="0 0 24 24"><circle cx="12" cy="12" r="9"/><path d="M3 12h18M12 3c3 3 3 15 0 18M12 3c-3 3-3 15 0 18"/></svg></span>
          WWW.TRV-GROUNDMAKRZ.COM
        </li>
      </ul>
    </div>
    <div class="front-band front-band--bottom"></div>
  </section>

  <section class="card card--back" aria-label="Business card back">
    <div class="brand">
      <span class="brand-mark"></span>
      <span class="brand-name">TRAVERSE GROUND<br>MAKRZ LLC</span>
      <span class="brand-phone">555-714-9082</span>
    </div>
    <div class="machine-art machine-art--left" role="img" aria-label="Black silhouette of a tracked excavator with raised arm"></div>
    <div class="machine-art machine-art--right" role="img" aria-label="Black outline of a tracked excavator digging with its bucket"></div>
    <div class="tagline-band">
      <p class="tagline">SPEACIALIZES IN LAND CLEARING ,MUCLHING &amp; EXCAVATION</p>
    </div>
  </section>

</body>
</html>
```